Redesign Website - Current one too plain

The description is in the uploaded file. Please let me know if you need any more information. I'd prefer it if someone could implement the design to a WordPress site but the best design will win, regardless.
I would like the forms to look nice as well
UPDATE:
I don't think we can use the images that I provided, I think they make the site look a bit 'cheap' and I really don't know how to replace them. One thought I have had is to make the "Simple, Unique, Effective" a second feature on the right side of the page with the search on the left
Target Market(s)
Small companies, private sellers of cars and people who rent their caravan/holiday home out
Industry/Entity Type
Advertising
Number of Pages Required
3 page
Colors
Designer to choose colors to be used in the design.
Look and feel
Each slider illustrates characteristics of the customer's brand and the style your logo design should communicate.

```html
<!DOCTYPE html>
<html lang="en">
<head>
<meta charset="utf-8">
<title>Markly – Discover And Connect</title>
<link href="https://fonts.googleapis.com/css2?family=Inter:wght@400;500;600;700&display=swap" rel="stylesheet">
<style>
  :root {
    --ink: #222222;
    --lime: #ebfb4e;
    --white: #ffffff;
    --text-dark: #111111;
    --photo-light: #c9c9c6;
    --photo-mid: #9d9c98;
  }
  * { margin: 0; padding: 0; box-sizing: border-box; }
  html, body { width: 1200px; height: 2397px; overflow: hidden; }
  body {
    background: var(--ink);
    color: var(--white);
    font-family: "Inter", Arial, sans-serif;
    position: relative;
  }
  .brand {
    position: absolute; left: 57px; top: 52px;
    display: flex; align-items: center; gap: 14px;
  }
  .brand-dot { width: 34px; height: 34px; border-radius: 50%; background: var(--lime); }
  .brand-name { color: var(--lime); font-size: 26px; font-weight: 500; }
  .main-nav {
    position: absolute; top: 66px; left: 438px;
    display: flex; gap: 0; font-size: 13.5px;
  }
  .main-nav a { color: var(--white); text-decoration: none; margin-right: 40px; }
  .main-nav a:nth-child(3) { margin-right: 55px; }
  .login-button {
    position: absolute; left: 1005px; top: 58px; width: 138px; height: 37px;
    border-radius: 19px; background: var(--lime); color: var(--ink);
    font-size: 17px; font-weight: 500; display: flex; align-items: center; justify-content: center;
  }
  .hero-title {
    position: absolute; top: 140px; width: 100%; text-align: center;
    font-size: 60px; font-weight: 700; letter-spacing: 0.3px;
  }
  .hero-subtitle {
    position: absolute; top: 222px; width: 100%; text-align: center; font-size: 17px;
  }
  .code-picker { position: absolute; top: 292px; left: 515px; display: flex; gap: 24px; }
  .code-slot { width: 60px; display: flex; flex-direction: column; align-items: center; }
  .code-char { color: var(--lime); font-size: 78px; font-weight: 500; line-height: 92px; }
  .chevron { width: 17px; height: 17px; }
  .category-chip {
    position: absolute; top: 438px; height: 33px; border: 1.5px solid var(--lime);
    border-radius: 17px; color: var(--lime); font-size: 17px;
    display: flex; align-items: center; justify-content: center;
  }
  .search-button {
    position: absolute; left: 481px; top: 499px; width: 237px; height: 37px;
    border-radius: 19px; background: var(--lime); color: var(--ink);
    font-size: 17px; font-weight: 500; display: flex; align-items: center; justify-content: center;
  }
  .hero-vehicles {
    position: absolute; left: 22px; top: 585px; width: 1113px; height: 500px;
    background: radial-gradient(ellipse at 55% 55%, var(--photo-light) 0%, var(--photo-mid) 55%, rgba(34,34,34,0) 75%);
    border-radius: 40% 40% 10% 10%;
  }
  .about-panel {
    position: absolute; left: 57px; top: 962px; width: 1086px; height: 481px;
    background: var(--white); border-radius: 30px; color: var(--text-dark);
  }
  .about-title {
    position: absolute; top: 62px; width: 100%; text-align: center; font-size: 27px; font-weight: 600;
  }
  .feature-card {
    position: absolute; top: 153px; width: 267px; height: 267px;
    background: var(--ink); border-radius: 30px; color: var(--white); text-align: center;
  }
  .feature-icon { position: absolute; top: 50px; left: 93px; width: 80px; height: 80px; }
  .feature-title {
    position: absolute; top: 150px; width: 100%; color: var(--lime); font-size: 22px; font-weight: 600;
  }
  .feature-text {
    position: absolute; top: 185px; left: 30px; right: 30px; font-size: 13.5px; line-height: 16px;
  }
  .how-title {
    position: absolute; top: 1502px; width: 100%; text-align: center;
    color: var(--lime); font-size: 27px; font-weight: 600;
  }
  .how-steps {
    position: absolute; top: 1551px; left: 60px; width: 1090px; font-size: 17px; line-height: 28.4px;
  }
  .how-steps p { margin-bottom: 28.4px; }
  .why-band {
    position: absolute; left: 0; top: 2000px; width: 1200px; height: 397px;
    background: var(--lime); color: var(--text-dark);
  }
  .why-title {
    position: absolute; top: 50px; width: 100%; text-align: center; font-size: 27px; font-weight: 600;
  }
  .why-body {
    position: absolute; top: 140px; left: 73px; width: 1060px; font-size: 17px; line-height: 28.4px;
  }
  .why-body ul { padding-left: 25px; }
</style>
</head>
<body>
  <header>
    <div class="brand"><span class="brand-dot"></span><span class="brand-name">Markly</span></div>
    <nav class="main-nav">
      <a href="#">Home</a><a href="#">Advertise</a><a href="#">Contact</a><a href="#">Register</a>
    </nav>
    <a class="login-button">Login</a>
  </header>

  <section class="hero">
    <h1 class="hero-title">Discover And Connect</h1>
    <p class="hero-subtitle">Display Your Unique Code on Your Vehicle to Attract Customers</p>
    <div class="code-picker">
      <div class="code-slot">
        <svg class="chevron" viewBox="0 0 17 17"><circle cx="8.5" cy="8.5" r="8.5" fill="#ebfb4e"/><path d="M5 10l3.5-3.5L12 10" stroke="#222" stroke-width="1.6" fill="none"/></svg>
        <span class="code-char">S</span>
        <svg class="chevron" viewBox="0 0 17 17"><circle cx="8.5" cy="8.5" r="8.5" fill="#ebfb4e"/><path d="M5 7l3.5 3.5L12 7" stroke="#222" stroke-width="1.6" fill="none"/></svg>
      </div>
      <div class="code-slot">
        <svg class="chevron" viewBox="0 0 17 17"><circle cx="8.5" cy="8.5" r="8.5" fill="#ebfb4e"/><path d="M5 10l3.5-3.5L12 10" stroke="#222" stroke-width="1.6" fill="none"/></svg>
        <span class="code-char">6</span>
        <svg class="chevron" viewBox="0 0 17 17"><circle cx="8.5" cy="8.5" r="8.5" fill="#ebfb4e"/><path d="M5 7l3.5 3.5L12 7" stroke="#222" stroke-width="1.6" fill="none"/></svg>
      </div>
    </div>
    <span class="category-chip" style="left:439px;width:55px">Car</span>
    <span class="category-chip" style="left:529px;width:93px">Caravan</span>
    <span class="category-chip" style="left:658px;width:102px">Company</span>
    <a class="search-button">Search</a>
    <div class="hero-vehicles" role="img" aria-label="Silver van, SUV and static caravan displayed together"></div>
  </section>

  <section class="about-panel">
    <h2 class="about-title">About us</h2>
    <div class="feature-card" style="left:76px">
      <svg class="feature-icon" viewBox="0 0 80 80" fill="none" stroke="#ebfb4e" stroke-width="2.5"><circle cx="40" cy="40" r="30"/><path d="M26 41l10 10 19-21"/></svg>
      <h3 class="feature-title">Simple</h3>
      <p class="feature-text">Create your advert and display your code</p>
    </div>
    <div class="feature-card" style="left:410px">
      <svg class="feature-icon" viewBox="0 0 80 80" fill="none" stroke="#ebfb4e" stroke-width="2.5"><circle cx="34" cy="34" r="20"/><path d="M49 49l18 18"/></svg>
      <h3 class="feature-title">Unique</h3>
      <p class="feature-text">Customers find you by an easy-to-remember code</p>
    </div>
    <div class="feature-card" style="left:743px">
      <svg class="feature-icon" viewBox="0 0 80 80" fill="none" stroke="#ebfb4e" stroke-width="2.5"><circle cx="40" cy="40" r="34"/><circle cx="40" cy="40" r="16"/><path d="M40 31v9l6 4"/></svg>
      <h3 class="feature-title">Effective</h3>
      <p class="feature-text">Customers are directed to you and not a list of your competitors</p>
    </div>
  </section>

  <section>
    <h2 class="how-title">How it works</h2>
    <div class="how-steps">
      <p>Step 1:<br>Create Your Advert Content:<br>Generate your unique code and create an eye-catching advert that showcases your business. Highlight your products, services, and contact details to ensure customers can easily reach you.</p>
      <p>Step 2:<br>Display Your Code Content:<br>Affix your code prominently on your vehicles. Whether it's a car, van, or caravan, your code will act as a beacon, guiding interested customers right to your doorstep.</p>
      <p>Step 3:<br>Customers Find Your Content:<br>Sit back and watch as customers effortlessly find and connect with your business using your memorable code. Increase your visibility and enhance your customer base with our innovative concept.</p>
    </div>
  </section>

  <section class="why-band">
    <h2 class="why-title">Why Choose Us</h2>
    <div class="why-body">
      <p>Our platform offers a user-friendly experience that empowers businesses of all sizes to increase their presence. With our easy-to-use system and eye-catching codes, you can enjoy these benefits:</p>
      <ul>
        <li>Stand out from competitors with a unique identifier</li>
        <li>Attract more customers with straightforward access to your business</li>
        <li>Increase your brand recognition and credibility</li>
        <li>Track the effectiveness of your adverts with real-time data</li>
      </ul>
    </div>
  </section>
</body>
</html>
```